RWT Fittings Ltd Business Cards

We need a business card with our business logo. We provide window and door installations on high-rises in west coast British Colombia, Canada.

I would like my business information and details on one side of the card, and the other side the company name with logo

Target Market(s)

General Contractors

Industry/Entity Type

Construction

Contact Information for Business Card

one side i want my company name and logo in the dark theme logo that i provided

Requirements
Must have
• Marco Peltieri, 16045518293, RWTFittings@mailbox-demo.com, 1407-5194 Linden Row Burnaby BC, V5H 2K9, Owner & Manager

```html
<!DOCTYPE html>
<html lang="en">
<head>
<meta charset="utf-8">
<title>RWT Fittings Ltd – Business Cards</title>
<link rel="stylesheet" href="https://fonts.googleapis.com/css2?family=Open+Sans:wght@400;700&display=swap">
<style>
  :root {
    --backdrop: #232323;
    --card: #1b1b1c;
    --brand-blue: #29a8e0;
    --ink-light: #f2f2f2;
  }
  * { box-sizing: border-box; margin: 0; padding: 0; }
  html, body { width: 1200px; height: 780px; overflow: hidden; }
  body {
    background: var(--backdrop);
    font-family: "Open Sans", Arial, sans-serif;
    position: relative;
  }
  .card {
    position: absolute;
    width: 520px;
    height: 300px;
    background: var(--card);
    border-radius: 22px;
    box-shadow: 0 14px 30px rgba(0,0,0,0.55);
    overflow: hidden;
  }
  .card--front { left: 60px; top: 110px; }
  .card--back  { left: 620px; top: 370px; }

  .brand {
    display: flex;
    align-items: center;
    gap: 14px;
    color: var(--brand-blue);
    font-weight: 700;
    white-space: nowrap;
  }
  .brand__mark { background: var(--brand-blue); flex: none; }

  .card--front .brand {
    position: absolute; inset: 0;
    justify-content: center;
    font-size: 44px;
  }
  .card--front .brand__mark { width: 34px; height: 34px; }

  .card--back .brand--small {
    position: absolute; right: 40px; top: 30px;
    font-size: 20px; gap: 10px;
  }
  .card--back .brand--small .brand__mark { width: 16px; height: 16px; }

  .brand--feature {
    position: absolute;
    left: 36px; bottom: 34px;
    width: 210px;
    flex-direction: column;
    align-items: flex-start;
    gap: 14px;
    font-size: 32px;
    line-height: 1.1;
    white-space: normal;
  }
  .brand--feature .brand__mark { width: 120px; height: 120px; }

  .details {
    position: absolute;
    right: 40px; top: 78px;
    width: 230px;
    text-align: right;
    color: var(--ink-light);
    font-size: 13px;
    line-height: 1.45;
  }
  .details__accent {
    position: absolute;
    right: -22px; top: 2px;
    width: 8px; height: 44px;
    background: var(--brand-blue);
  }
  .details__name {
    color: var(--brand-blue);
    font-weight: 700;
    font-size: 19px;
    letter-spacing: 0.3px;
    line-height: 1.15;
  }
  .details__title { font-size: 14px; margin-bottom: 12px; }
  .details__address { margin-bottom: 12px; }
  .contact-line {
    display: flex; justify-content: flex-end; align-items: center; gap: 7px;
    white-space: nowrap;
  }
  .contact-line svg { width: 12px; height: 12px; flex: none; }
  .icon-fill { fill: var(--brand-blue); }
  .icon-cut { fill: none; stroke: var(--card); stroke-width: 1.8; }
</style>
</head>
<body>

  <section class="card card--front" aria-label="Business card front">
    <div class="brand">
      <span class="brand__mark"></span>
      <span class="brand__name">RWT Fittings Ltd</span>
    </div>
  </section>

  <section class="card card--back" aria-label="Business card back">
    <div class="brand brand--feature">
      <span class="brand__mark"></span>
      <span class="brand__name">RWT Fittings Ltd</span>
    </div>

    <div class="brand brand--small">
      <span class="brand__mark"></span>
      <span class="brand__name">RWT Fittings Ltd</span>
    </div>

    <div class="details">
      <span class="details__accent"></span>
      <p class="details__name">MARCO PELTIERI</p>
      <p class="details__title">Owner &amp; Manager</p>
      <p class="details__address">1407-5194 Linden Row<br>Burnaby BC, V5H 2K9</p>
      <p class="contact-line">16045518293
        <svg viewBox="0 0 24 24" aria-hidden="true"><path class="icon-fill" d="M6.6 10.8a15 15 0 0 0 6.6 6.6l2.2-2.2a1 1 0 0 1 1-.25 11.4 11.4 0 0 0 3.6.57 1 1 0 0 1 1 1V20a1 1 0 0 1-1 1A17 17 0 0 1 3 4a1 1 0 0 1 1-1h3.5a1 1 0 0 1 1 1c0 1.25.2 2.45.57 3.6a1 1 0 0 1-.25 1z"/></svg>
      </p>
      <p class="contact-line">RWTFittings@mailbox-demo.com
        <svg viewBox="0 0 24 24" aria-hidden="true"><rect class="icon-fill" x="2" y="5" width="20" height="14" rx="1.5"/><path class="icon-cut" d="M3 6.5l9 7 9-7"/></svg>
      </p>
      <p class="contact-line">www.yourwebsite.com
        <svg viewBox="0 0 24 24" aria-hidden="true"><circle class="icon-fill" cx="12" cy="12" r="10"/><path class="icon-cut" d="M2 12h20M12 2c3.5 3 3.5 17 0 20M12 2c-3.5 3-3.5 17 0 20"/></svg>
      </p>
    </div>
  </section>

</body>
</html>
```